Upmarket Dessert Lounge needs a Business Card Design

We are an upmarket dessert lounge needing a business card to match our image.

We want something that is simple yet beautiful, feminine, classy, sophisticated and elegant. We want it to stand out and don't mind if it is bold.

The design should include our logo and colours of red or maroon with gold highlights. We don't mind if black is used.

Marlow & Quince

Target Market(s)

For those who like to indulge or treat themselves and give in to their temptations on good quality desserts.

Industry/Entity Type

Business

Requirements
Must have
• Must include our logo and our name

Marlow & Quince

M & Q

```html
<!DOCTYPE html>
<html lang="en">
<head>
<meta charset="utf-8">
<title>Marlow &amp; Quince – Business Card</title>
<link rel="stylesheet" href="https://fonts.googleapis.com/css2?family=Crimson+Text:wght@600;700&family=PT+Sans:wght@400&display=swap">
<style>
  :root {
    --maroon: #7a1416;
    --maroon-deep: #5e0e10;
    --cream: #f6d6a4;
    --paper: #ffffff;
    --ink: #333333;
    --backdrop: #ece7e2;
  }
  html, body {
    margin: 0;
    width: 1200px;
    height: 758px;
    overflow: hidden;
    background: var(--backdrop);
  }
  .canvas {
    position: relative;
    width: 1200px;
    height: 758px;
  }
  .card {
    position: absolute;
    width: 520px;
    height: 300px;
    border-radius: 26px;
    overflow: hidden;
    box-shadow: 0 8px 22px rgba(0,0,0,.18);
  }
  .card-front { left: 50px; top: 229px; background: var(--paper); }
  .card-back  { left: 630px; top: 229px; background: var(--maroon); }

  .front-wave {
    position: absolute;
    left: 0; bottom: 0;
    width: 520px; height: 110px;
  }
  .brand-name {
    position: absolute;
    left: 0; right: 0; top: 40px;
    text-align: center;
    font-family: "Crimson Text", serif;
    font-weight: 600;
    font-size: 38px;
    letter-spacing: 1px;
    color: var(--maroon);
  }
  .person {
    position: absolute;
    left: 0; right: 0; top: 112px;
    text-align: center;
    font-family: "Crimson Text", serif;
    font-size: 20px;
    color: var(--maroon);
  }
  .person-name { font-weight: 700; letter-spacing: 1px; }
  .person-title {
    font-family: "PT Sans", sans-serif;
    font-size: 14px;
    color: var(--ink);
  }
  .address {
    position: absolute;
    right: 266px; top: 172px;
    text-align: right;
    font-family: "PT Sans", sans-serif;
    font-size: 14px;
    line-height: 18px;
    color: var(--ink);
  }
  .divider {
    position: absolute;
    left: 264px; top: 156px;
    width: 1px; height: 54px;
    background: #bdbdbd;
  }
  .contacts {
    position: absolute;
    left: 274px; top: 154px;
    margin: 0; padding: 0;
    list-style: none;
    font-family: "PT Sans", sans-serif;
    font-size: 13px;
    line-height: 18px;
    color: var(--ink);
  }
  .contacts li { display: flex; align-items: center; gap: 5px; }
  .contacts svg { width: 11px; height: 11px; fill: var(--ink); }
  .front-web {
    position: absolute;
    right: 28px; top: 256px;
    font-family: "PT Sans", sans-serif;
    font-size: 14px;
    letter-spacing: .5px;
    color: var(--paper);
  }
  .monogram {
    position: absolute;
    left: 0; right: 0; top: 78px;
    text-align: center;
    font-family: "Crimson Text", serif;
    font-weight: 600;
    font-size: 84px;
    color: var(--paper);
  }
  .back-web {
    position: absolute;
    left: 0; right: 0; top: 224px;
    text-align: center;
    font-family: "PT Sans", sans-serif;
    font-size: 21px;
    letter-spacing: 2.5px;
    color: var(--paper);
  }
</style>
</head>
<body>
<main class="canvas">

  <section class="card card-front" aria-label="Card front">
    <svg class="front-wave" viewBox="0 0 520 110" preserveAspectRatio="none" aria-hidden="true">
      <path d="M0 96 C150 104 270 34 520 18 L520 110 L0 110 Z" fill="var(--cream)"/>
      <path d="M0 103 C160 110 280 44 520 28 L520 110 L0 110 Z" fill="var(--maroon)"/>
    </svg>

    <div class="brand-name">Marlow &amp; Quince</div>

    <div class="person">
      <span class="person-name">Your name,</span>
      <span class="person-title">Title</span>
    </div>

    <div class="address">Street Name, City Name<br>State Zip Code</div>
    <div class="divider"></div>

    <ul class="contacts">
      <li>
        <svg viewBox="0 0 24 24" aria-hidden="true"><path d="M6.6 10.8a15.1 15.1 0 006.6 6.6l2.2-2.2a1 1 0 011-.25 11.4 11.4 0 003.6.57 1 1 0 011 1V20a1 1 0 01-1 1A17 17 0 013 4a1 1 0 011-1h3.5a1 1 0 011 1 11.4 11.4 0 00.57 3.6 1 1 0 01-.25 1z"/></svg>
        555-014-2270
      </li>
      <li>
        <svg viewBox="0 0 24 24" aria-hidden="true"><path d="M7 1h10a2 2 0 012 2v18a2 2 0 01-2 2H7a2 2 0 01-2-2V3a2 2 0 012-2zm0 4v13h10V5z"/></svg>
        555-014-2270
      </li>
      <li>
        <svg viewBox="0 0 24 24" aria-hidden="true"><path d="M2 5h20v14H2zm2 2v.5l8 5 8-5V7z"/></svg>
        info@marlow&amp;quince.com
      </li>
    </ul>

    <div class="front-web">www.marlow&amp;quince.com</div>
  </section>

  <section class="card card-back" aria-label="Card back">
    <div class="monogram">M &amp; Q</div>
    <div class="back-web">www.marlow&amp;quince.com</div>
  </section>

</main>
</body>
</html>
```